Design für Geburtskarte A6 hoch, Klappkarte
Zielgruppe
Ich bin Fotograf und habe mich auf Schwangerschafts- und Neugeborenenfotografie spezialisiert. Meine Zielgruppe sind schwangere Frauen im letzten Drittel der Schwangerschaft und frisch gewordene Eltern.
Aufgabenstellung
- sehr schlichtes Design, in der Anlage finden Sie zwei der meist verkauften Karten damit Sie sich vom Stil eine Vorstellung machen können
- Lieferung als offene Indesign 5.5 Datei (so das die Farben, Texte, .... angepasst werden können)
- 2-3 Bilder (querformat) sollen in das Design eingearbeitet werden können
- Die Karten werden von mir nachher als fertig gedruckte Karte an meine Kunden verkauft, dies bitte ich zu berücksichtigen
- ich möchte die Karten so nutzen können das sowohl Geburtskarten für Jungs wie auch für Mädels erstellt werden können
- Format: Din A6 (geschlossen 105x148mm), Klappkarte, hoch, 3mm Beschnitt

```html
<!DOCTYPE html>
<html lang="de">
<head>
<meta charset="utf-8">
<title>Geburtskarte – Klappkarte A6 hoch</title>
<link href="https://fonts.googleapis.com/css2?family=Sacramento&family=Josefin+Sans:wght@300&family=Roboto:wght@300&display=swap" rel="stylesheet">
<style>
  :root {
    --bg: #efefef;
    --label: #8d8d8d;
    --chalk-dark: #262626;
    --chalk-mid: #373737;
    --chalk-light: #464646;
    --chalk-text: #f4f4f4;
    --chalk-soft: #dcdcdc;
    --rose: #b98aa2;
    --rose-line: #7d5a6c;
    --teal: #8fc4bb;
    --teal-line: #5e8f87;
  }
  * { margin: 0; padding: 0; box-sizing: border-box; }
  html, body { width: 1200px; height: 829px; overflow: hidden; }
  body { background: var(--bg); font-family: "Roboto", Arial, sans-serif; position: relative; }

  .theme-girl { --accent: var(--rose); --accent-line: var(--rose-line); }
  .theme-boy  { --accent: var(--teal); --accent-line: var(--teal-line); }

  /* ---------- page base: 243 × 342 ---------- */
  .page { position: absolute; top: 0; width: 243px; height: 342px; overflow: hidden;
    background:
      radial-gradient(ellipse at 30% 25%, rgba(255,255,255,.07), transparent 55%),
      radial-gradient(ellipse at 75% 80%, rgba(255,255,255,.05), transparent 60%),
      linear-gradient(160deg, var(--chalk-light), var(--chalk-mid) 45%, var(--chalk-dark)); }
  .photo { position: absolute; }
  .dots-h { position: absolute; left: 0; right: 0; height: 2px;
    background: radial-gradient(circle, #fff 0.8px, transparent 1.1px) 0 0 / 6.5px 2px repeat-x; }
  .dots-v { position: absolute; width: 2px;
    background: radial-gradient(circle, #fff 0.8px, transparent 1.1px) 0 0 / 2px 6.5px repeat-y; }
  .badge { position: absolute; border-radius: 50%; background: var(--accent);
    display: flex; align-items: center; justify-content: center; }
  .badge svg { display: block; fill: #fff; }
  .script { font-family: "Sacramento", cursive; }

  /* back */
  .back__badge { width: 20px; height: 20px; left: 111px; top: 299px; }
  .back__studio { position: absolute; top: 322px; width: 100%; text-align: center; font-size: 6px; color: var(--chalk-text); }
  .back__dots { top: 333px; left: 10px; right: 4px; }

  /* front */
  .front__photo { left: 0; top: 0; width: 243px; height: 214px; }
  .front__dots { top: 213px; }
  .front__badge { width: 47px; height: 47px; left: 98px; top: 190px; }
  .front__name { position: absolute; top: 244px; width: 100%; text-align: center;
    font-family: "Sacramento", cursive; font-weight: 400; font-size: 58px; color: var(--chalk-text); line-height: 1; }
  .front__underline { top: 297px; left: 75px; right: 74px; }

  /* inner left */
  .il__hero { left: 0; top: 0; width: 243px; height: 209px; }
  .il__dots { top: 213px; }
  .il__small-a { left: 0; top: 217px; width: 88px; height: 125px; }
  .il__divider { left: 91px; top: 217px; height: 125px; }
  .il__small-b { left: 95px; top: 217px; width: 148px; height: 125px; }

  /* inner right */
  .ir__thanks { position: absolute; top: 36px; width: 100%; text-align: center;
    font-family: "Sacramento", cursive; font-weight: 400; font-size: 60px; color: var(--chalk-text); line-height: 1; }
  .ir__text { position: absolute; top: 96px; width: 100%; text-align: center; font-size: 8.6px; line-height: 11.5px; color: var(--chalk-soft); }
  .ir__parents { position: absolute; top: 132px; width: 100%; text-align: center; font-size: 8.6px; color: #e6e6e6; }
  .ir__badge { width: 14px; height: 14px; left: 115px; top: 148px; }
  .ir__dots { top: 213px; }
  .facts { position: absolute; left: 22px; right: 23px; top: 0; height: 342px; color: #e8e8e8; }
  .facts__row { position: absolute; left: 0; right: 0; display: flex; align-items: center; justify-content: space-between; }
  .facts__row--top { top: 245px; }
  .facts__row--bottom { top: 287px; }
  .fact { font-size: 12.5px; font-weight: 300; letter-spacing: .3px; white-space: nowrap; }
  .fact .script { font-size: 19px; }
  .ruler { position: absolute; top: 272px; left: 0; width: 198px; height: 9px; }
  .ruler rect { fill: var(--accent); }
  .ruler line { stroke: var(--accent-line); stroke-width: 1; }
  .accent-fill { fill: var(--accent); }

  /* photo tones */
  .tone-basket   { background: linear-gradient(170deg, #b49a86, #d7c6b6 45%, #9b6f8f 75%, #8f7766); }
  .tone-lilac    { background: radial-gradient(ellipse at 45% 60%, #e9cfc3, #d8c6e2 75%, #f1ecf3); }
  .tone-peach    { background: linear-gradient(160deg, #e7a9b5, #d39a72 55%, #7e5a3f); }
  .tone-white    { background: linear-gradient(150deg, #d9c9bd, #eee8e6 50%, #f6f2f0); }
  .tone-amber    { background: linear-gradient(160deg, #b6794a, #d9935a 40%, #e7b08a 70%, #8a5a3a); }
  .tone-fleece   { background: radial-gradient(ellipse at 55% 50%, #e2c6b4, #ece6dd 60%, #f4f1ec); }
  .tone-cuddle   { background: linear-gradient(160deg, #6b4a3c, #c99a84 50%, #e6cbbd); }
  .tone-blanket  { background: linear-gradient(160deg, #d8c4b8, #ece3dc 55%, #f3efeb); }

  /* ---------- layout ---------- */
  .mini { position: absolute; top: 96px; height: 226px; }
  .mini .page { transform: scale(.66); transform-origin: 0 0; box-shadow: 0 2px 6px rgba(0,0,0,.18); }
  .mini--closed { width: 215px; }
  .mini--open { width: 321px; }

  .page-label { position: absolute; top: 390px; width: 243px; text-align: center;
    font-family: "Josefin Sans", Arial, sans-serif; font-weight: 300; font-size: 18px; color: var(--label); letter-spacing: .4px; }

  .spread { position: absolute; top: 417px; width: 486px; height: 342px; box-shadow: 0 2px 8px rgba(0,0,0,.12); }
  .spread--outer { left: 71px; }
  .spread--inner { left: 610px; }
</style>
</head>
<body>

<svg width="0" height="0" style="position:absolute" aria-hidden="true">
  <symbol id="heart" viewBox="0 0 24 22"><path d="M12 21 C5 15 1 11 1 6.5 1 3.4 3.4 1 6.4 1 8.6 1 10.8 2.3 12 4.4 13.2 2.3 15.4 1 17.6 1 20.6 1 23 3.4 23 6.5 23 11 19 15 12 21Z"/></symbol>
  <symbol id="clock" viewBox="0 0 24 24"><circle cx="12" cy="12" r="11" fill="#fff"/><circle cx="12" cy="12" r="8.5" fill="none" stroke="#2c2c2c" stroke-width="1.4"/><path d="M12 6.5V12L9.5 14.5" stroke="#2c2c2c" stroke-width="1.5" fill="none" stroke-linecap="round"/></symbol>
</svg>

<!-- ===== top row: folded views ===== -->
<div class="mini mini--closed theme-girl" style="left:20px">
  <section class="page" style="left:55px">
    <div class="facts">
      <div class="facts__row facts__row--top"><span class="fact">24. <span class="script">Juni</span> 2016</span><svg width="22" height="22"><use href="#clock"/></svg><span class="fact">17.03 <span class="script">Uhr</span></span></div>
      <svg class="ruler" viewBox="0 0 198 9" aria-hidden="true"><rect width="198" height="9"/></svg>
      <div class="facts__row facts__row--bottom"><span class="fact">3690 <span class="script">Gramm</span></span><span></span><span class="fact">52 <span class="script">cm</span></span></div>
    </div>
    <div class="dots-h ir__dots"></div>
  </section>
  <section class="page">
    <div class="photo front__photo tone-basket" role="img" aria-label="Foto: Neugeborenes schlafend in einer Holzschale"></div>
    <div class="dots-h front__dots"></div>
    <div class="badge front__badge"><svg width="26" height="24"><use href="#heart"/></svg></div>
    <p class="front__name">Lina</p>
    <div class="dots-h front__underline"></div>
  </section>
</div>

<div class="mini mini--open theme-girl" style="left:265px">
  <section class="page">
    <div class="photo il__hero tone-lilac" role="img" aria-label="Foto: Baby mit lila Haarband"></div>
    <div class="dots-h il__dots"></div>
    <div class="photo il__small-a tone-peach" role="img" aria-label="Foto: schlafendes Baby"></div>
    <div class="dots-v il__divider"></div>
    <div class="photo il__small-b tone-white" role="img" aria-label="Foto: Babyfüße auf Fell"></div>
  </section>
  <section class="page" style="left:160px">
    <p class="ir__thanks">Danke</p>
    <p class="ir__text">für die Glückwünsche und Geschenke<br>zur Geburt unserer Tochter.</p>
    <p class="ir__parents">Mara &amp; Jonas</p>
    <div class="badge ir__badge"><svg width="8" height="7"><use href="#heart"/></svg></div>
    <div class="dots-h ir__dots"></div>
    <div class="facts">
      <div class="facts__row facts__row--top"><span class="fact">24. <span class="script">Juni</span> 2016</span><svg width="22" height="22"><use href="#clock"/></svg><span class="fact">17.03 <span class="script">Uhr</span></span></div>
      <svg class="ruler" viewBox="0 0 198 9" aria-hidden="true"><rect width="198" height="9"/></svg>
      <div class="facts__row facts__row--bottom"><span class="fact">3690 <span class="script">Gramm</span></span><svg width="24" height="26" viewBox="0 0 26 28"><path class="accent-fill" d="M3 2H23L16 12V14H10V12Z"/><path class="accent-fill" d="M4 27L8 17H18L22 27Z"/><circle cx="13" cy="21.5" r="3.2" fill="#fff"/></svg><span class="fact">52 <span class="script">cm</span></span></div>
    </div>
  </section>
</div>

<div class="mini mini--closed theme-boy" style="left:616px">
  <section class="page" style="left:55px">
    <div class="facts">
      <div class="facts__row facts__row--top"><span class="fact">24. <span class="script">Juni</span> 2016</span><svg width="22" height="22"><use href="#clock"/></svg><span class="fact">17.03 <span class="script">Uhr</span></span></div>
      <svg class="ruler" viewBox="0 0 198 9" aria-hidden="true"><rect width="198" height="9"/></svg>
      <div class="facts__row facts__row--bottom"><span class="fact">3690 <span class="script">Gramm</span></span><span></span><span class="fact">52 <span class="script">cm</span></span></div>
    </div>
    <div class="dots-h ir__dots"></div>
  </section>
  <section class="page">
    <div class="photo front__photo tone-amber" role="img" aria-label="Foto: Neugeborener Junge schlafend auf einer Decke"></div>
    <div class="dots-h front__dots"></div>
    <div class="badge front__badge"><svg width="26" height="24"><use href="#heart"/></svg></div>
    <p class="front__name">Henrik</p>
    <div class="dots-h front__underline"></div>
  </section>
</div>

<div class="mini mini--open theme-boy" style="left:861px">
  <section class="page">
    <div class="photo il__hero tone-fleece" role="img" aria-label="Foto: Baby auf weißem Fell"></div>
    <div class="dots-h il__dots"></div>
    <div class="photo il__small-a tone-cuddle" role="img" aria-label="Foto: Mutter mit Baby"></div>
    <div class="dots-v il__divider"></div>
    <div class="photo il__small-b tone-blanket" role="img" aria-label="Foto: Baby in heller Decke"></div>
  </section>
  <section class="page" style="left:160px">
    <p class="ir__thanks">Danke</p>
    <p class="ir__text">für die Glückwünsche und Geschenke<br>zur Geburt unseres Sohnes.</p>
    <p class="ir__parents">Nele &amp; Tom</p>
    <div class="badge ir__badge"><svg width="8" height="7"><use href="#heart"/></svg></div>
    <div class="dots-h ir__dots"></div>
    <div class="facts">
      <div class="facts__row facts__row--top"><span class="fact">24. <span class="script">Juni</span> 2016</span><svg width="22" height="22"><use href="#clock"/></svg><span class="fact">17.03 <span class="script">Uhr</span></span></div>
      <svg class="ruler" viewBox="0 0 198 9" aria-hidden="true"><rect width="198" height="9"/></svg>
      <div class="facts__row facts__row--bottom"><span class="fact">3690 <span class="script">Gramm</span></span><svg width="24" height="26" viewBox="0 0 26 28"><path class="accent-fill" d="M3 2H23L16 12V14H10V12Z"/><path class="accent-fill" d="M4 27L8 17H18L22 27Z"/><circle cx="13" cy="21.5" r="3.2" fill="#fff"/></svg><span class="fact">52 <span class="script">cm</span></span></div>
    </div>
  </section>
</div>

<!-- ===== labels ===== -->
<div class="page-label" style="left:71px">Rückseite</div>
<div class="page-label" style="left:314px">Vorderseite</div>
<div class="page-label" style="left:610px">Innenseite links</div>
<div class="page-label" style="left:853px">Innenseite rechts</div>

<!-- ===== flat spreads ===== -->
<div class="spread spread--outer theme-girl">
  <section class="page" style="left:0">
    <div class="badge back__badge"><svg width="12" height="11"><use href="#heart"/></svg></div>
    <p class="back__studio">Falkner Fotografie</p>
    <div class="dots-h back__dots"></div>
  </section>
  <section class="page" style="left:243px">
    <div class="photo front__photo tone-basket" role="img" aria-label="Foto: Neugeborenes schlafend in einer Holzschale mit Fell und lila Tuch"></div>
    <div class="dots-h front__dots"></div>
    <div class="badge front__badge"><svg width="26" height="24"><use href="#heart"/></svg></div>
    <h1 class="front__name">Lina</h1>
    <div class="dots-h front__underline"></div>
  </section>
</div>

<div class="spread spread--inner theme-girl">
  <section class="page" style="left:0">
    <div class="photo il__hero tone-lilac" role="img" aria-label="Foto: Baby mit lila Blumen-Haarband"></div>
    <div class="dots-h il__dots"></div>
    <div class="photo il__small-a tone-peach" role="img" aria-label="Foto: schlafendes Baby mit rosa Haarband"></div>
    <div class="dots-v il__divider"></div>
    <div class="photo il__small-b tone-white" role="img" aria-label="Foto: Babyfüße auf weißem Fell"></div>
  </section>
  <section class="page" style="left:243px">
    <h2 class="ir__thanks">Danke</h2>
    <p class="ir__text">für die Glückwünsche und Geschenke<br>zur Geburt unserer Tochter.</p>
    <p class="ir__parents">Mara &amp; Jonas</p>
    <div class="badge ir__badge"><svg width="8" height="7"><use href="#heart"/></svg></div>
    <div class="dots-h ir__dots"></div>
    <div class="facts">
      <div class="facts__row facts__row--top"><span class="fact">24. <span class="script">Juni</span> 2016</span><svg width="22" height="22"><use href="#clock"/></svg><span class="fact">17.03 <span class="script">Uhr</span></span></div>
      <svg class="ruler" viewBox="0 0 198 9" aria-hidden="true">
        <rect width="198" height="9"/>
        <line x1="10" y1="0" x2="10" y2="3"/><line x1="20" y1="0" x2="20" y2="3"/><line x1="30" y1="0" x2="30" y2="3"/><line x1="40" y1="0" x2="40" y2="3"/><line x1="50" y1="0" x2="50" y2="5"/><line x1="60" y1="0" x2="60" y2="3"/><line x1="70" y1="0" x2="70" y2="3"/><line x1="80" y1="0" x2="80" y2="3"/><line x1="90" y1="0" x2="90" y2="3"/><line x1="100" y1="0" x2="100" y2="5"/><line x1="110" y1="0" x2="110" y2="3"/><line x1="120" y1="0" x2="120" y2="3"/><line x1="130" y1="0" x2="130" y2="3"/><line x1="140" y1="0" x2="140" y2="3"/><line x1="150" y1="0" x2="150" y2="5"/><line x1="160" y1="0" x2="160" y2="3"/><line x1="170" y1="0" x2="170" y2="3"/><line x1="180" y1="0" x2="180" y2="3"/><line x1="190" y1="0" x2="190" y2="3"/>
      </svg>
      <div class="facts__row facts__row--bottom"><span class="fact">3690 <span class="script">Gramm</span></span><svg width="24" height="26" viewBox="0 0 26 28" aria-hidden="true"><path class="accent-fill" d="M3 2H23L16 12V14H10V12Z"/><path class="accent-fill" d="M4 27L8 17H18L22 27Z"/><circle cx="13" cy="21.5" r="3.2" fill="#fff"/><line x1="13" y1="21.5" x2="13" y2="19" stroke="#555" stroke-width="0.8"/></svg><span class="fact">52 <span class="script">cm</span></span></div>
    </div>
  </section>
</div>

</body>
</html>
```